Business Card Design for Property Development Company Director

I am looking for a professional and unforgettable business card design for our Director of our Property Development Company.
Please see attached .pptx file to find out what information to include. You don't have to follow the exact format shown in the file - I am interested to see your creative flair using the information provided.

```html
<!DOCTYPE html>
<html lang="en">
<head>
<meta charset="utf-8">
<title>Halvern Property Group – Business Card</title>
<link rel="stylesheet" href="https://fonts.googleapis.com/css2?family=Lato:wght@400;700;900&family=Montserrat:wght@600;700&display=swap">
<style>
  :root {
    --brand-blue: #1158a6;
    --brand-blue-dark: #0d4a8f;
    --ink-grey: #5c5c5c;
    --text-dark: #333333;
    --rule-grey: #7a7a7a;
    --card-white: #ffffff;
    --faint-mark: #eef0f4;
    --backdrop: #0b0b0b;
  }
  * { box-sizing: border-box; margin: 0; padding: 0; }
  html, body { width: 1200px; height: 895px; overflow: hidden; background: var(--backdrop); }
  body { font-family: "Lato", sans-serif; position: relative; }

  .card {
    position: absolute;
    left: 280px;
    width: 640px;
    height: 366px;
    border-radius: 22px;
    overflow: hidden;
  }

  /* Front */
  .card--front { top: 50px; background: var(--brand-blue); color: #fff; text-align: center; }
  .front__tagline {
    position: absolute; top: 58px; left: 0; right: 0;
    font-size: 19px; font-weight: 700; letter-spacing: 0.6px; line-height: 1.3;
  }
  .front__brand {
    position: absolute; top: 140px; left: 0; right: 0;
    display: flex; align-items: center; justify-content: center; gap: 18px;
  }
  .brand__square { width: 58px; height: 58px; background: #fff; }
  .brand__text { text-align: left; }
  .brand__name { font-size: 60px; font-weight: 900; line-height: 0.95; letter-spacing: 1px; }
  .brand__sub { font-size: 20px; font-weight: 400; letter-spacing: 5.5px; margin-top: 4px; }
  .front__cta {
    position: absolute; bottom: 52px; left: 0; right: 0;
    font-size: 16px; letter-spacing: 0.6px;
  }

  /* Back */
  .card--back { top: 478px; background: var(--card-white); color: var(--text-dark); }
  .back__edge { position: absolute; left: 0; right: 0; bottom: 0; height: 7px; background: var(--brand-blue); }
  .back__mark { position: absolute; top: 30px; right: 60px; width: 150px; height: 150px; background: var(--faint-mark); }
  .back__brand { position: absolute; top: 44px; left: 38px; display: flex; align-items: center; gap: 14px; }
  .back__brand .brand__square { width: 44px; height: 44px; background: var(--brand-blue); }
  .back__brand .brand__name { font-size: 44px; color: var(--brand-blue); }
  .back__brand .brand__sub { font-size: 15px; letter-spacing: 4.5px; color: var(--brand-blue); }

  .back__person { position: absolute; top: 170px; right: 40px; text-align: right; }
  .person__name { font-family: "Montserrat", sans-serif; font-weight: 700; font-size: 30px; color: var(--brand-blue); letter-spacing: -0.5px; }
  .person__role { font-size: 17px; color: var(--text-dark); margin-top: 2px; }
  .person__licence { font-size: 14px; margin-top: 10px; color: var(--text-dark); }
  .person__licence span { color: var(--brand-blue); }

  .back__rule { position: absolute; left: 38px; right: 40px; top: 262px; height: 2px; background: var(--rule-grey); }

  .back__contact { position: absolute; left: 38px; top: 276px; list-style: none; font-size: 17px; line-height: 1.55; }
  .back__contact li { display: flex; align-items: center; gap: 10px; }
  .back__contact svg { width: 15px; height: 15px; fill: var(--brand-blue); flex: none; }
</style>
</head>
<body>

<section class="card card--front" aria-label="Business card front">
  <p class="front__tagline">Property Development<br>&amp; Site Acquisition Specialists</p>
  <div class="front__brand">
    <span class="brand__square"></span>
    <div class="brand__text">
      <div class="brand__name">HALVERN</div>
      <div class="brand__sub">PROPERTY GROUP</div>
    </div>
  </div>
  <p class="front__cta">Ask me about our INVESTMENT &amp; PARTNERSHIP opportunities</p>
</section>

<section class="card card--back" aria-label="Business card back">
  <span class="back__mark" aria-hidden="true"></span>
  <div class="back__brand">
    <span class="brand__square"></span>
    <div class="brand__text">
      <div class="brand__name">HALVERN</div>
      <div class="brand__sub">PROPERTY GROUP</div>
    </div>
  </div>

  <div class="back__person">
    <div class="person__name">DANIEL MARSH</div>
    <div class="person__role">Director</div>
    <div class="person__licence"><span>Real Estate Lic:</span> 5512038 &amp; 5512039</div>
  </div>

  <div class="back__rule"></div>

  <ul class="back__contact">
    <li>
      <svg viewBox="0 0 16 16" aria-hidden="true"><path d="M3.5 1.5l2.3 2.6-1.3 1.8c.9 2 2.6 3.7 4.6 4.6l1.8-1.3 2.6 2.3-1.2 2.5C7 13.5 2.5 9 1 3.7z"/></svg>
      0400 218 736
    </li>
    <li>
      <svg viewBox="0 0 16 16" aria-hidden="true"><path d="M1 3h14v10H1zM2.5 4.5v.3L8 9l5.5-4.2v-.3z"/></svg>
      daniel@halvern.com.au
    </li>
    <li>
      <svg viewBox="0 0 16 16" aria-hidden="true"><path d="M8 1a7 7 0 100 14A7 7 0 008 1zm0 1.5c.8 0 1.7 1.6 2 4H6c.3-2.4 1.2-4 2-4zM6 9.5h4c-.3 2.4-1.2 4-2 4s-1.7-1.6-2-4zM2.6 6.5h2c0-.8.1-1.6.3-2.3a5.6 5.6 0 00-2.3 2.3zm8.8 0h2a5.6 5.6 0 00-2.3-2.3c.2.7.3 1.5.3 2.3zM2.6 9.5a5.6 5.6 0 002.3 2.3c-.2-.7-.3-1.5-.3-2.3zm8.8 0c0 .8-.1 1.6-.3 2.3a5.6 5.6 0 002.3-2.3z"/></svg>
      www.halvern.com.au
    </li>
  </ul>
  <div class="back__edge"></div>
</section>

</body>
</html>
```